LEARN Business Skills so you can Earn a good living

size of the poster is 8”x 10.75" plus 0.25" bleed.
Please leave 1 inch on the bottoum for footer
I want a design a poster that will attract people's attention.
I appreciate a creative ad however the ad should not take away from being able to clearly read the text.
-I also appreciate a simple creative ad that is not too busy.
-you can use graphics, vectors, or pictures of real people.
-however, if you use real people it should be a white male that is wearing a white shirt and look like a professional person.

Target Market(s)

Potential young business people

Industry/Entity Type

education

Requirements
Must have
• easy to read the text
Nice to have
• I would like a "creative" simple ad that is easy to be read
Should not have
• pictures of women

```html
<!DOCTYPE html>
<html lang="en">
<head>
<meta charset="utf-8">
<title>Business Enrichment Course Poster</title>
<link href="https://fonts.googleapis.com/css2?family=DM+Sans:wght@400;500;700&family=Dancing+Script:wght@500&family=Playfair+Display:wght@900&display=swap" rel="stylesheet">
<style>
  :root {
    --backdrop: #7f7f7f;
    --paper: #ececec;
    --paper-light: #f3f3f3;
    --brand-blue: #2f4d8a;
    --title-blue: #2e5597;
    --navy: #1f3566;
    --icon-blue: #2f55a0;
    --accent-orange: #e88a2c;
    --ink: #253049;
    --rule: #c9cbd0;
  }
  * { margin: 0; padding: 0; box-sizing: border-box; }
  html, body { width: 1200px; height: 1200px; overflow: hidden; }
  body { background: var(--backdrop); font-family: "DM Sans", sans-serif; }

  .poster {
    position: absolute; left: 174px; top: 0;
    width: 852px; height: 1200px;
    background: linear-gradient(180deg, var(--paper-light), var(--paper));
    overflow: hidden;
  }
  .city-backdrop {
    position: absolute; left: 180px; top: 0; width: 680px; height: 700px;
    background: radial-gradient(ellipse at 50% 55%, rgba(190,192,198,.45), rgba(236,236,236,0) 70%);
  }
  .brand-block {
    position: absolute; left: 564px; top: 56px; width: 288px; height: 201px;
    background: var(--brand-blue);
    border-left: 16px solid var(--accent-orange);
    display: flex; align-items: center; justify-content: center;
  }
  .brand-name {
    color: #fff; font-weight: 700; font-size: 40px; line-height: 1.05;
    text-align: center; letter-spacing: 1px;
  }
  .course-title {
    position: absolute; left: 54px; top: 338px; z-index: 2;
    font-family: "Playfair Display", serif; font-weight: 900;
    font-size: 78px; line-height: 80px; letter-spacing: -1px;
    color: var(--title-blue);
  }
  .hero-illustration {
    position: absolute; left: 610px; top: 346px; width: 200px; height: 224px;
    background: linear-gradient(135deg, #d4dbe8 0%, #3a63b0 60%, #203a78 100%);
    clip-path: polygon(0 100%, 100% 0, 100% 100%);
  }
  .tagline {
    position: absolute; left: 0; right: 0; top: 600px; text-align: center;
    font-family: "Dancing Script", cursive; font-weight: 500;
    font-size: 33px; color: var(--accent-orange);
  }
  .benefits {
    position: absolute; left: 0; top: 690px; width: 852px; height: 192px;
  }
  .benefit {
    position: absolute; top: 4px; width: 260px; margin-left: -130px;
    text-align: center;
  }
  .benefit-icon {
    width: 118px; height: 118px; margin: 0 auto;
    border-radius: 34px 34px 0 34px;
    background: linear-gradient(135deg, var(--navy), var(--icon-blue));
    display: flex; align-items: center; justify-content: center;
  }
  .benefit-label {
    margin-top: 12px; font-size: 25px; line-height: 29px;
    font-weight: 500; color: var(--ink);
  }
  .divider {
    position: absolute; top: 0; width: 1px; height: 192px; background: var(--rule);
  }
  .course-list {
    position: absolute; left: 0; right: 0; top: 930px;
    text-align: center; font-size: 17.5px; line-height: 30px;
    color: var(--ink); white-space: nowrap;
  }
  .sep { color: var(--accent-orange); padding: 0 3px; }
</style>
</head>
<body>
<main class="poster">
  <div class="city-backdrop" role="img" aria-label="Faded photograph of a city skyline with a tall skyscraper"></div>

  <div class="brand-block">
    <span class="brand-name">SKILL<br>LADDER</span>
  </div>

  <h1 class="course-title">BUSINESS<br>ENRICHMENT<br>COURSE</h1>

  <div class="hero-illustration" role="img" aria-label="Illustration of a businessman in a white shirt with a laptop, sitting on a rising blue arrow, with a briefcase beside bar graphs"></div>

  <p class="tagline">A proven success of helping people in their livelihoods</p>

  <section class="benefits">
    <div class="divider" style="left:264px"></div>
    <div class="divider" style="left:550px"></div>

    <div class="benefit" style="left:134px">
      <div class="benefit-icon">
        <svg width="64" height="64" viewBox="0 0 64 64" fill="none" stroke="#fff" stroke-width="4" stroke-linecap="round" stroke-linejoin="round">
          <circle cx="32" cy="32" r="24"/>
          <path d="M21 33l8 8 15-17" stroke="#e88a2c"/>
        </svg>
      </div>
      <p class="benefit-label">Get a<br>Quality Job</p>
    </div>

    <div class="benefit" style="left:407px">
      <div class="benefit-icon">
        <svg width="64" height="64" viewBox="0 0 64 64" fill="none" stroke="#fff" stroke-width="4" stroke-linecap="round" stroke-linejoin="round">
          <rect x="10" y="10" width="44" height="44" rx="8"/>
          <path d="M32 21v22M21 32h22" stroke="#e88a2c"/>
        </svg>
      </div>
      <p class="benefit-label">Start/Grow<br>Your Business</p>
    </div>

    <div class="benefit" style="left:692px">
      <div class="benefit-icon">
        <svg width="64" height="64" viewBox="0 0 64 64" fill="none" stroke="#fff" stroke-width="4" stroke-linecap="round" stroke-linejoin="round">
          <path d="M32 54V12"/>
          <path d="M18 26l14-14 14 14" stroke="#e88a2c"/>
        </svg>
      </div>
      <p class="benefit-label">Increase Your<br>Salary</p>
    </div>
  </section>

  <p class="course-list">
    Business Administration<span class="sep">|</span>Small Business Management<span class="sep">|</span>Finance<span class="sep">|</span>Investments<span class="sep">|</span><br>
    Computers<span class="sep">|</span>Accounting<span class="sep">|</span>Sales Marketing<span class="sep">|</span>Project Management Interviewing Skills<span class="sep">|</span><br>
    Business Law<span class="sep">|</span>Negotiation<span class="sep">|</span>Public Speaking<span class="sep">|</span>Import/Export<span class="sep">|</span>Information Technoloy<span class="sep">|</span><br>
    Distribution<span class="sep">|</span>Marketing<span class="sep">|</span>Ledgerly<span class="sep">|</span>Real Estate<span class="sep">|</span>Health Care<span class="sep">|</span>Management<span class="sep">|</span>Shopora
  </p>
</main>
</body>
</html>
```